FernPath....... a dash of Glow

I need a web design for a new business based in London that will be mobile (offered at homes, parks or a local cafe ect) called FernPath. I offer Life Coaching/Counselling sessions, Personal training, Massage and Sports Massage. Sessions range from an hour to half and hour. My aim is to help people along their journey to help give them gain clarity of where there going, helping them to towards their goals, so that can experience bliss. My website should represent a place people can come to release their stress and worries so that they leave feeling lighter, clearer and happier. I would like my website to reflect someone feeling ALIVE. I would also like a logo design for FernPath with a sentence underneath or near saying A dash of Glow.

Target Market(s)

middle class people

Industry/Entity Type

Business

Coding

Coded - Design and coding required

Number of Pages Required

4 page

Requirements
Must have
• 1st page About us
• 2nd page Services
• 3rd page Prices
• 4th page contact details
Nice to have
• mixture of cultures in images

```html
<!DOCTYPE html>
<html lang="en">
<head>
<meta charset="utf-8">
<title>FernPath — a dash of Glow</title>
<link href="https://fonts.googleapis.com/css2?family=Questrial&family=Dancing+Script:wght@400;700&display=swap" rel="stylesheet">
<style>
:root{
  --teal:#3dbfa7;
  --teal-dark:#2fa892;
  --gold:#d4a43d;
  --gold-soft:#ddb15a;
  --ink:#3a3a3a;
  --muted:#666;
  --white:#fff;
  --field:#f1f1f1;
}
*{margin:0;padding:0;box-sizing:border-box}
html,body{width:1200px;height:2239px;overflow:hidden;background:var(--white)}
body{font-family:'Questrial',sans-serif;color:var(--ink);position:relative}
.abs{position:absolute}
.script{font-family:'Dancing Script',cursive}

/* header */
.site-header{position:absolute;left:0;top:0;width:1200px;height:143px;background:var(--white)}
.topbar{position:absolute;left:0;top:0}
.topbar-item{position:absolute;top:14px;color:var(--white);font-size:17px;display:flex;align-items:center;gap:9px}
.social-dot{width:13px;height:13px;border-radius:50%;background:var(--white);display:inline-block}
.brand{position:absolute;left:118px;top:34px;width:100px;text-align:center}
.brand-name{font-size:31px;color:var(--teal);line-height:1}
.brand-tag{font-size:9px;color:var(--ink);margin-top:8px}
.main-nav{position:absolute;top:90px;left:0;font-size:14px;letter-spacing:.3px}
.main-nav a{position:absolute;white-space:nowrap;color:#333;text-decoration:none}
.main-nav a.is-active{color:var(--teal)}

/* hero */
.hero{position:absolute;left:0;top:143px;width:1200px;height:591px}
.hero-photo{position:absolute;inset:0;background:linear-gradient(180deg,#e9b84a 0%,#f6d27a 40%,#fbe4a4 62%,#e2a53a 82%,#b57420 100%)}
.hero-sun{position:absolute;left:640px;top:150px;width:420px;height:420px;border-radius:50%;background:radial-gradient(circle,#fff8de 0%,rgba(255,240,190,.6) 40%,rgba(255,230,160,0) 70%)}
.hero-figure{position:absolute;left:560px;top:20px;width:420px;height:571px;background:radial-gradient(ellipse at 60% 50%,rgba(60,35,15,.75) 0%,rgba(60,35,15,.35) 35%,rgba(60,35,15,0) 62%)}
.hero-kicker{position:absolute;left:149px;top:362px;font-size:52px;color:#4a3b35}
.hero-title{position:absolute;left:145px;top:418px;font-size:74px;color:var(--teal);letter-spacing:2px}
.hero-dots{position:absolute;left:527px;top:694px;display:flex;gap:21px}
.hero-dots span{width:12px;height:12px;border-radius:50%;border:2px solid #444}
.hero-dots span.is-current{background:var(--teal);border-color:var(--teal)}

/* services */
.section-title{position:absolute;left:0;width:1200px;text-align:center;font-size:44px}
.section-title .gold{color:var(--gold)}
.section-title .teal{color:var(--teal)}
.section-lead{position:absolute;left:0;width:1200px;top:832px;text-align:center;font-size:13.5px;color:#555}
.divider{position:absolute;left:465px;top:864px}
.service{position:absolute;top:907px;width:300px;text-align:center}
.service-photo{width:200px;height:200px;border-radius:50%;border:4px solid var(--gold);margin:0 auto}
.service-name{margin-top:36px;font-size:18px;color:#333;letter-spacing:.3px}

/* about band */
.about-band{position:absolute;left:0;top:1236px;width:1200px;height:458px;background:var(--teal)}
.about-band-shade{position:absolute;inset:0;background:radial-gradient(ellipse at 75% 40%,rgba(255,255,255,.12),rgba(255,255,255,0) 55%)}
.about-photo{position:absolute;left:79px;top:70px;width:518px;height:318px;border:2px solid #c9b35c;background:radial-gradient(ellipse at 55% 70%,#b5465a 0%,#5a2530 35%,#161616 70%)}
.about-title{position:absolute;left:643px;top:70px;font-size:58px;color:var(--white)}
.about-title .soft{color:#2a6f63}
.about-rule{position:absolute;left:645px;top:145px}
.about-text{position:absolute;left:645px;top:180px;width:473px;font-size:12.5px;line-height:29px;color:var(--white);text-align:justify}
.btn-more{position:absolute;left:642px;top:343px;width:164px;height:42px;border-radius:21px;background:var(--gold);color:var(--white);font-size:14px;display:flex;align-items:center;justify-content:center;gap:7px}

/* contact strip */
.contact-strip{position:absolute;left:0;top:1694px;width:1200px;height:187px;background:var(--white)}
.strip-label{position:absolute;top:54px;font-size:13px;color:#555}
.strip-value{position:absolute;top:88px;font-size:20px;color:#222;display:flex;align-items:center;gap:8px}
.strip-note{position:absolute;top:118px;font-size:11px;color:#333}
.subscribe{position:absolute;left:752px;top:86px;width:366px;height:38px;background:var(--field);border:1px solid #e4e4e4}
.subscribe span{position:absolute;left:18px;top:12px;font-size:11px;color:#999}

/* footer */
.site-footer{position:absolute;left:0;top:1881px;width:1200px;height:358px;background:var(--gold)}
.footer-glow{position:absolute;left:560px;top:20px;width:380px;height:338px;background:radial-gradient(ellipse,rgba(200,140,40,.55),rgba(200,140,40,0) 65%)}
.footer-brand{position:absolute;left:117px;top:84px;width:160px;text-align:center;color:var(--white)}
.footer-brand .name{font-size:34px}
.footer-brand .copy{font-size:12.5px;line-height:20px;margin-top:50px}
.footer-title{position:absolute;font-size:30px;color:#3a2f20}
.footer-list{position:absolute;list-style:none;font-size:13px;color:var(--white)}
.footer-list li{height:36.5px;display:flex;gap:12px}
.footer-list li::before{content:"›";font-size:15px;line-height:14px}
.footer-social{position:absolute;left:391px;top:2009px;display:flex;gap:31px}
.footer-social span{width:15px;height:15px;border-radius:50%;background:var(--white)}
.timing{position:absolute;left:391px;top:2109px;font-size:13px;color:var(--white);line-height:24px}
.timing td{padding-right:14px}
</style>
</head>
<body>

<header class="site-header">
  <svg class="topbar" width="1200" height="50" viewBox="0 0 1200 50">
    <path d="M321 0 H1200 V50 H470 C400 50 350 30 321 0 Z" fill="var(--teal)"/>
    <line x1="608" y1="8" x2="608" y2="42" stroke="#ffffff" stroke-opacity=".35"/>
    <line x1="888" y1="8" x2="888" y2="42" stroke="#ffffff" stroke-opacity=".35"/>
  </svg>
  <div class="topbar-item" style="left:492px;gap:22px"><span class="social-dot"></span><span class="social-dot"></span><span class="social-dot"></span></div>
  <div class="topbar-item" style="left:657px">
    <svg width="17" height="13" viewBox="0 0 17 13"><rect width="17" height="13" rx="1.5" fill="#fff"/><path d="M1 1 L8.5 7 L16 1" stroke="#3dbfa7" stroke-width="1.5" fill="none"/></svg>
    support@fernpath.com
  </div>
  <div class="topbar-item" style="left:936px">
    <svg width="16" height="16" viewBox="0 0 24 24"><path fill="#fff" d="M6.6 10.8a15 15 0 0 0 6.6 6.6l2.2-2.2c.3-.3.7-.4 1-.2 1.1.4 2.3.6 3.6.6.6 0 1 .4 1 1V20c0 .6-.4 1-1 1C10.6 21 3 13.4 3 4c0-.6.4-1 1-1h3.5c.6 0 1 .4 1 1 0 1.3.2 2.5.6 3.6.1.3 0 .7-.2 1z"/></svg>
    (800) 555-0147
  </div>
  <div class="brand">
    <div class="brand-name">FernPath</div>
    <div class="brand-tag">a dash of Glow</div>
  </div>
  <nav class="main-nav">
    <a class="is-active" style="left:495px">HOME</a>
    <a style="left:609px">ABOUT US</a>
    <a style="left:752px">SERVICES</a>
    <a style="left:893px">PRICES</a>
    <a style="left:1016px">CONTACT</a>
  </nav>
</header>

<section class="hero">
  <div class="hero-photo" role="img" aria-label="Photo of a woman with arms raised against a golden sunset sky">
    <div class="hero-sun"></div>
    <div class="hero-figure"></div>
  </div>
  <div class="hero-kicker script">A dash of</div>
  <div class="hero-title">GLOW</div>
</section>
<div class="hero-dots"><span></span><span></span><span class="is-current"></span><span></span><span></span></div>

<section class="services">
  <h2 class="section-title script" style="top:763px"><span class="gold">Our</span> <span class="teal">Services</span></h2>
  <p class="section-lead">A wonderful sereny has taken possession of soul, like these sweet mornings of idma aute rure dolor in reprehendet</p>
  <svg class="divider" width="270" height="16" viewBox="0 0 270 16">
    <line x1="20" y1="8" x2="250" y2="8" stroke="var(--gold)" stroke-width="1.2"/>
    <path d="M2 8 L10 3 L10 13 Z M268 8 L260 3 L260 13 Z" fill="var(--gold)"/>
  </svg>
  <div class="service" style="left:96px">
    <div class="service-photo" role="img" aria-label="Photo of a life coaching conversation" style="background:linear-gradient(135deg,#e8e2dc,#8b6a5a 55%,#3b2a24)"></div>
    <div class="service-name">LIFE COACHING</div>
  </div>
  <div class="service" style="left:444px">
    <div class="service-photo" role="img" aria-label="Photo of women stretching in a fitness studio" style="background:linear-gradient(160deg,#f3f4f7,#c9c3d6 50%,#6e6a78)"></div>
    <div class="service-name">PERSONAL TRAINING</div>
  </div>
  <div class="service" style="left:793px">
    <div class="service-photo" role="img" aria-label="Photo of a woman relaxing at a spa beside green plants" style="background:linear-gradient(160deg,#7fae55,#c9b79a 55%,#6a4a3a)"></div>
    <div class="service-name">MASSAGE AND SPORTS MASSAGE</div>
  </div>
</section>

<section class="about-band">
  <div class="about-band-shade"></div>
  <div class="about-photo" role="img" aria-label="Portrait photo of the coach in a pink top at night"></div>
  <h2 class="about-title script">Fern<span class="soft">Path</span></h2>
  <svg class="about-rule" width="475" height="10" viewBox="0 0 475 10">
    <path d="M0 5 L8 1 L8 9 Z M10 5 L18 1 L18 9 Z" fill="#fff"/>
    <line x1="22" y1="5" x2="475" y2="5" stroke="#fff" stroke-width="1"/>
  </svg>
  <p class="about-text">It is our goal at FernPath to help you through your journey in life by empowering you to reach your goals and achieve what you desire in life, whether it is through life coaching, personal training, or Angel reading guidance. We also offer massage and sports massage to help you relax and rejuvenate, experience a dash of glow, and develop a better you.</p>
  <div class="btn-more">Read More
    <svg width="12" height="12" viewBox="0 0 12 12"><circle cx="6" cy="6" r="6" fill="#fff"/><path d="M4.5 3 L7.5 6 L4.5 9" stroke="var(--gold)" stroke-width="1.6" fill="none"/></svg>
  </div>
</section>

<section class="contact-strip">
  <div class="strip-label" style="left:81px">Book by Phone</div>
  <div class="strip-value" style="left:81px">
    <svg width="15" height="15" viewBox="0 0 24 24"><path fill="var(--gold)" d="M6.6 10.8a15 15 0 0 0 6.6 6.6l2.2-2.2c.3-.3.7-.4 1-.2 1.1.4 2.3.6 3.6.6.6 0 1 .4 1 1V20c0 .6-.4 1-1 1C10.6 21 3 13.4 3 4c0-.6.4-1 1-1h3.5c.6 0 1 .4 1 1 0 1.3.2 2.5.6 3.6.1.3 0 .7-.2 1z"/></svg>
    0 700 555 0192
  </div>
  <div class="strip-note" style="left:106px">Booking time: 8am - 9pm</div>

  <div class="strip-label" style="left:327px">Services and Support</div>
  <div class="strip-value" style="left:327px">
    <svg width="15" height="11" viewBox="0 0 17 13"><rect width="17" height="13" rx="1.5" fill="var(--gold)"/><path d="M1 1 L8.5 7 L16 1" stroke="#fff" stroke-width="1.5" fill="none"/></svg>
    fernpath.adashofglow@mailbox.com
  </div>
  <div class="strip-note" style="left:351px">Get your doubts cleared</div>

  <div class="strip-label" style="left:754px">Subscribe for the best Deals</div>
  <div class="subscribe"><span>Enter Your Email Address</span>
    <svg style="position:absolute;right:14px;top:10px" width="18" height="16" viewBox="0 0 18 16"><path d="M0 7 L18 0 L13 16 L9 10 Z" fill="var(--gold)"/></svg>
  </div>
  <div class="strip-note" style="left:755px;top:136px">Subscribe to our email newsletter</div>
</section>

<footer class="site-footer">
  <div class="footer-glow"></div>
  <div class="footer-brand">
    <div class="name">FernPath</div>
    <div class="copy">© 2015<br>Allrights Reserved</div>
  </div>
  <div class="footer-title script" style="left:391px;top:62px">Follow us</div>
  <div class="footer-title script" style="left:391px;top:175px">Timing</div>
  <div class="footer-title script" style="left:695px;top:62px">Navigation</div>
  <div class="footer-title script" style="left:913px;top:62px">Services</div>
  <ul class="footer-list" style="left:695px;top:129px">
    <li>About</li><li>Classes</li><li>Gallery</li><li>Testimonials</li><li>Contact us</li>
  </ul>
  <ul class="footer-list" style="left:913px;top:129px">
    <li>Life / personal Performance</li><li style="padding-left:19px">Coaching</li><li>Angel Readings</li><li>Personal training</li><li>Sports Massage &amp; Massage</li>
  </ul>
</footer>
<div class="footer-social"><span></span><span></span><span></span></div>
<table class="timing">
  <tr><td>Mon - Fri</td><td>:</td><td>6:00am - 11:00pm</td></tr>
  <tr><td>Sat</td><td>:</td><td>7:00am - 10:00pm</td></tr>
  <tr><td>Sun</td><td>:</td><td>Closed</td></tr>
</table>

</body>
</html>
```